Dusty Spur Outfitters Home Page

I need a logo and page design for my home page, maybe some background color suggestions to go with it. I want the logo to project "vintage" and "western wear" but not be your typical trite western saddle and gun type thing.
http://www.dustyspuroutfitters.example/store/cart.php
Not looking for page coding just logo and other design elements to lay in over the site's template to make it "pop"
Reason: Have to finalize the design.
Target Market(s)
My customers are 70/30 men to women.
Industry/Entity Type
Gun

```html
<!DOCTYPE html>
<html lang="en">
<head>
<meta charset="utf-8">
<title>Dusty Spur Outfitters</title>
<link href="https://fonts.googleapis.com/css2?family=Crimson+Text:wght@400;600&family=Open+Sans:wght@400;600&family=Oswald:wght@400&display=swap" rel="stylesheet">
<style>
:root{
  --wood:#3a1a12;
  --wood-dark:#2a110b;
  --cream:#f6e6c8;
  --paper:#fbf6ee;
  --red:#a8161c;
  --maroon:#3d1710;
  --ink:#2b1a14;
  --muted:#8a7a6c;
  --gold:#b89a4a;
  --olive:#8c9a2a;
  --footer:#5a2c20;
}
*{box-sizing:border-box;margin:0;padding:0}
html,body{width:720px;height:1200px;overflow:hidden}
body{background:linear-gradient(90deg,var(--wood-dark),var(--wood) 30%,var(--wood) 70%,var(--wood-dark));font-family:"Open Sans",sans-serif;color:var(--ink);position:relative}
.abs{position:absolute}
.topbar a{color:#eee;font-size:8px;text-decoration:none;position:absolute;top:15px}
.search{left:430px;top:10px;width:150px;height:20px;background:var(--wood-dark);border-radius:3px;color:#ddd;font-size:8px;padding:5px 8px}
.cart{left:600px;top:15px;color:#eee;font-size:7px}
.page{left:61px;top:100px;width:600px;height:800px;background:var(--cream)}
.footer{left:61px;top:900px;width:600px;height:260px;background:var(--footer);border-top:3px solid var(--olive)}
.ribbon{left:36px;top:40px;width:652px;height:65px;background:var(--paper);box-shadow:0 2px 4px rgba(0,0,0,.3);clip-path:polygon(0 10%,3% 10%,3% 0,97% 0,97% 10%,100% 10%,98% 55%,100% 100%,0 100%,2% 55%)}
.nav{top:62px;font-size:11px;color:#6b5a50}
.nav.home{color:var(--red)}
.star{top:62px;font-size:8px;color:#999}
.logo{left:318px;top:20px;width:84px;height:96px;border-radius:50%;background:var(--paper);border:2px solid #e3d2bd;display:flex;align-items:center;justify-content:center;text-align:center;font-family:"Crimson Text",serif;font-weight:600;color:var(--red);font-size:14px;line-height:1.05}
.hero{left:68px;top:99px;width:586px;height:259px;background:radial-gradient(circle at 70% 45%,#e8a090,#7a4a5a 40%,#3a2a3a 80%)}
.hero-box{left:87px;top:150px;width:305px;height:130px;background:rgba(60,40,50,.35)}
.hero-title{left:87px;top:155px;font-family:"Crimson Text",serif;font-weight:400;font-size:30px;color:#fff;white-space:nowrap}
.hero-sub{left:87px;top:207px;color:#fff;font-size:13px}
.hero-copy{left:87px;top:232px;width:280px;color:#eee;font-size:8px;line-height:1.5}
.btn{top:270px;height:20px;font-size:8.5px;color:#fff;display:flex;align-items:center;justify-content:center}
.dot{top:340px;width:13px;height:13px;border-radius:50%;border:1px solid #fff;color:#fff;font-size:6px;display:flex;align-items:center;justify-content:center}
.arrow{top:217px;width:26px;height:26px;border-radius:50%;display:flex;align-items:center;justify-content:center;color:#fff;font-size:10px}
.cats{left:69px;top:405px;width:157px;height:353px;background:var(--maroon)}
.cats h2{background:var(--red);height:28px;color:#fff;font-family:"Crimson Text",serif;font-weight:400;font-size:15px;text-align:center;line-height:28px}
.cats ul{list-style:none;margin-top:12px}
.cats li{font-family:"Crimson Text",serif;font-size:8.5px;color:#eadbc8;height:16.2px;line-height:16.2px;padding-left:26px;position:relative}
.cats li::before{content:"";position:absolute;left:11px;top:5px;width:6px;height:6px;border-radius:50%;background:#6b4a40}
.cats li.active{background:var(--red)}
.cats li.active::before{background:#fff}
.manu{position:absolute;left:0;top:330px;width:157px;height:23px;background:#2a0f0a;color:#eee;font-family:"Crimson Text",serif;font-size:8.5px;padding:5px 8px}
.manu span{position:absolute;left:73px;top:5px;width:78px;height:13px;background:#3d1710}
.products-title{left:237px;top:402px;font-family:"Crimson Text",serif;font-size:15px;color:#7a5a40}
.rule{left:237px;top:423px;width:415px;height:1px;background:#b59a80}
.card{width:128px;height:120px;background:#fff;padding:5px;box-shadow:0 1px 3px rgba(0,0,0,.2)}
.card div{width:100%;height:100%}
.cap{width:140px;text-align:center;font-family:"Crimson Text",serif;font-size:7.5px;color:var(--muted);line-height:1.4;white-space:nowrap}
.cap b{display:block;font-weight:400;font-size:10px;color:var(--ink)}
.feat{top:800px;width:129px;height:64px;color:#fff;text-align:center}
.feat h3{font-weight:400;font-size:10px;text-decoration:underline;margin-top:10px}
.feat p{font-size:7px;line-height:1.6;margin-top:4px}
.fh{top:925px;font-family:"Oswald",sans-serif;font-size:15px;color:#fff;letter-spacing:-.5px}
.date{width:52px;height:44px;background:var(--cream);border-radius:50%;text-align:center;font-family:"Oswald",sans-serif;font-size:15px;color:var(--maroon);padding-top:4px}
.date small{display:block;font-size:6px;background:var(--gold);color:#fff}
.post{width:110px;font-family:"Crimson Text",serif;color:#f0e0d0;font-size:6.5px;line-height:1.3}
.post b{display:block;font-weight:400;color:var(--gold);font-size:8.5px;margin-bottom:5px}
.form{left:467px;top:961px;width:177px;height:175px;background:var(--paper);padding:12px 17px;font-size:6px;color:#666}
.form .f{border-bottom:1px solid #ccc;height:21px;padding-top:6px}
.send{position:absolute;left:0;bottom:0;width:177px;height:28px;background:#f0dfc0;border-top:3px dashed var(--red);font-family:"Oswald",sans-serif;font-size:12px;color:var(--maroon);padding:4px 22px}
.copy{top:1176px;font-size:6.5px;color:#eee}
</style>
</head>
<body>
<div class="topbar"><a style="left:70px">REGISTER</a><a style="left:141px">LOGIN</a></div>
<div class="abs search">Search Here</div>
<div class="abs cart">CART (0) &#128722;</div>

<div class="abs page"></div>
<div class="abs hero" role="img" aria-label="Photo of a woman in a coral top carrying shopping bags on a city street at night"></div>
<div class="abs hero-box"></div>
<div class="abs hero-title">Dusty Spur Outfitters</div>
<div class="abs hero-sub">Mobile Application Development</div>
<div class="abs hero-copy">Lorem ipsum dolor sit amet, consectetur adipiscing elit. Sed justo ipsum, mollis ac volutpat sed, pulvinar sed mauris.</div>
<div class="abs btn" style="left:85px;width:89px;background:var(--red)">Search All</div>
<div class="abs btn" style="left:182px;width:89px;background:#111">Read More</div>
<div class="abs dot" style="left:312px">1</div><div class="abs dot" style="left:342px;background:var(--red)">2</div><div class="abs dot" style="left:372px">3</div><div class="abs dot" style="left:402px">4</div><div class="abs dot" style="left:432px">5</div>
<div class="abs arrow" style="left:46px;background:var(--red)">&#8249;</div>
<div class="abs arrow" style="left:654px;background:#2a0f0a">&#8250;</div>

<div class="abs ribbon"></div>
<div class="abs nav home" style="left:87px">Home</div><div class="abs star" style="left:141px">&#9733;</div>
<div class="abs nav" style="left:167px">Shipping</div><div class="abs star" style="left:235px">&#9733;</div>
<div class="abs nav" style="left:261px">Sizing</div>
<div class="abs nav" style="left:424px">Contact</div><div class="abs star" style="left:493px">&#9733;</div>
<div class="abs nav" style="left:521px">About</div><div class="abs star" style="left:566px">&#9733;</div>
<div class="abs nav" style="left:598px">Links</div>
<div class="abs logo">Dusty Spur<br>Outfitters</div>

<div class="abs cats">
  <h2>Categories</h2>
  <ul>
    <li>Boots</li><li>Men's Western Wear</li><li>Women's Western Wear</li><li>Brand New Arrivals</li><li>CLEARANCE</li><li class="active">T-Shirts</li><li>Vests</li><li>Accessories</li><li>Jackets</li><li>BELTS</li><li>Hand Bags</li><li>Leather</li><li>On Sale!</li><li>Pants</li><li>Short Sleeves</li><li>Big and Tall</li><li>Jeans</li>
  </ul>
  <div class="manu">Manufacturer<span></span></div>
</div>

<div class="abs products-title">Our Products</div>
<div class="abs rule"></div>
<div class="abs" style="left:627px;top:408px;width:10px;height:10px;border-radius:50%;background:var(--red)"></div>
<div class="abs" style="left:640px;top:408px;width:10px;height:10px;border-radius:50%;background:#666"></div>

<div class="abs card" style="left:237px;top:433px"><div role="img" aria-label="Product photo: man in a white hat and black western suit" style="background:linear-gradient(#e8e8e8,#2a2a2a)"></div></div>
<div class="abs card" style="left:382px;top:433px"><div role="img" aria-label="Product photo: man in a two-tone blue western shirt" style="background:linear-gradient(#8ac8e8,#d8c8a8)"></div></div>
<div class="abs card" style="left:526px;top:433px"><div role="img" aria-label="Product photo: blue jeans with a western belt buckle" style="background:linear-gradient(#e8e8e8,#4a5a70)"></div></div>
<div class="abs card" style="left:237px;top:608px"><div role="img" aria-label="Product photo: woman in a red embroidered western blouse" style="background:linear-gradient(#7a4a20,#a0282a)"></div></div>
<div class="abs card" style="left:382px;top:608px"><div role="img" aria-label="Product photo: stack of printed graphic t-shirts" style="background:linear-gradient(135deg,#c04030,#d0b040,#5a8ab0)"></div></div>
<div class="abs card" style="left:526px;top:608px"><div role="img" aria-label="Product photo: grey t-shirt with a rodeo print" style="background:linear-gradient(#6a7a8a,#4a5060)"></div></div>
<div class="abs" style="left:277px;top:540px;width:22px;height:22px;background:var(--red);color:#fff;font-size:8px;text-align:center;line-height:22px">&#128722;</div>
<div class="abs" style="left:301px;top:540px;width:22px;height:22px;background:var(--maroon);color:#fff;font-size:8px;text-align:center;line-height:22px">i</div>

<div class="abs cap" style="left:231px;top:566px">Midi Bodycon Dress With Poloneck<br>And Long Sleeves<b>$250</b></div>
<div class="abs cap" style="left:375px;top:566px">Midi Bodycon Dress With Poloneck<br>And Long Sleeves<b>$250</b></div>
<div class="abs cap" style="left:519px;top:566px">Midi Bodycon Dress With Poloneck<br>And Long Sleeves<b>$250</b></div>
<div class="abs cap" style="left:231px;top:740px">Midi Bodycon Dress With Poloneck<br>And Long Sleeves<b>$250</b></div>
<div class="abs cap" style="left:375px;top:740px">Midi Bodycon Dress With Poloneck<br>And Long Sleeves<b>$250</b></div>
<div class="abs cap" style="left:519px;top:740px">Midi Bodycon Dress With Poloneck<br>And Long Sleeves<b>$250</b></div>

<div class="abs feat" style="left:69px;background:var(--red)">
  <svg class="abs" style="left:9px;top:20px" width="44" height="26" viewBox="0 0 44 26" fill="#fff"><rect x="0" y="2" width="26" height="16"/><path d="M28 7h9l6 7v4H28z"/><circle cx="8" cy="21" r="4" stroke="var(--red)" stroke-width="2"/><circle cx="35" cy="21" r="4" stroke="var(--red)" stroke-width="2"/></svg>
  <div class="abs" style="left:56px;top:10px;font-size:10px;line-height:1.5;text-align:center;width:70px"><u>Free Shipping</u><br>order<br>over $49</div>
</div>
<div class="abs feat" style="left:220px;background:#1a1a1a">
  <svg class="abs" style="left:9px;top:22px" width="26" height="24" viewBox="0 0 26 24" fill="none" stroke="#fff" stroke-width="1.5"><path d="M4 14a9 9 0 0 1 18 0"/><rect x="2" y="13" width="5" height="8" rx="2"/><rect x="19" y="13" width="5" height="8" rx="2"/></svg>
  <h3 style="margin-left:20px">Support 24/24</h3><p style="margin-left:20px">Lorem ipsum dolor sit<br>amit enuram ti adse</p>
</div>
<div class="abs feat" style="left:372px;background:#1a1a1a">
  <div class="abs" style="left:14px;top:14px;font-size:30px">?</div>
  <h3 style="margin-left:15px">Trailpost like</h3><p style="margin-left:15px">Like us on Trailpost<br>and get 5% off your</p>
</div>
<div class="abs feat" style="left:523px;background:#1a1a1a">
  <h3>Newsletter</h3>
  <svg class="abs" style="left:8px;top:31px" width="24" height="17" viewBox="0 0 24 17" fill="none" stroke="#fff" stroke-width="1.5"><rect x="1" y="1" width="22" height="15"/><path d="M1 1l11 9 11-9M1 16l8-7M23 16l-8-7"/></svg>
  <div class="abs" style="left:39px;top:40px;width:65px;height:13px;background:#fff"></div>
  <div class="abs" style="left:104px;top:40px;width:16px;height:13px;background:var(--red);color:#fff;font-size:7px;text-align:center;line-height:13px">&#9654;</div>
</div>

<div class="abs footer"></div>
<div class="abs fh" style="left:80px">RECENT POSTS</div>
<div class="abs fh" style="left:310px">RATINGS</div>
<div class="abs fh" style="left:468px">GET IN TOUCH</div>

<div class="abs date" style="left:80px;top:962px">24<small>august</small></div>
<div class="abs post" style="left:148px;top:961px"><b>Marigold Lane picks her favourites from this week's</b>The singer, fashion blogger and clothes designer Marigold Lane (aka Rosa Hartley) picks her favourites</div>
<div class="abs" style="left:80px;top:1034px;width:175px;border-top:1px dashed #8a5a48"></div>
<div class="abs date" style="left:80px;top:1048px">02<small>august</small></div>
<div class="abs post" style="left:148px;top:1047px"><b>The singer, fashion blogger</b>The singer, fashion blogger and clothes designer Marigold Lane (aka Rosa Hartley) picks her favourites</div>

<div class="abs" style="left:309px;top:966px;width:95px;height:36px;background:#1f4e6e;border-radius:4px"></div>
<div class="abs" style="left:311px;top:1023px;width:40px;height:37px;background:#e8e0d0"></div>
<div class="abs fh" style="left:310px;top:1072px">WE ACCEPT</div>
<div class="abs" style="left:311px;top:1102px;width:18px;height:11px;background:#fff"></div>
<div class="abs" style="left:334px;top:1102px;width:18px;height:11px;background:#fff"></div>
<div class="abs" style="left:358px;top:1102px;width:18px;height:11px;background:#fff"></div>

<div class="abs form">
  <div class="f">Name:</div><div class="f">Email:</div><div class="f" style="margin-top:2px">Your message...</div><div class="f"></div><div class="f"></div>
  <div class="abs" style="left:137px;top:17px;width:28px;height:28px;border:2px dashed #ccc;font-size:10px;text-align:center;line-height:24px">&#9993;</div>
  <div class="send">- SEND -<span class="abs" style="right:8px;top:10px;font-family:'Open Sans',sans-serif;font-size:6px">* all fields are required</span></div>
</div>

<div class="abs copy" style="left:62px">Copyright © yourwebsite &nbsp;&nbsp;&nbsp;&nbsp; View Cart &nbsp; | &nbsp; Site Search &nbsp; | &nbsp; My Account &nbsp; | &nbsp; Featured Products &nbsp; | &nbsp; Contact Us &nbsp; Privacy</div>
<div class="abs" style="left:575px;top:1173px;width:13px;height:13px;border-radius:50%;background:var(--gold)"></div>
<div class="abs" style="left:599px;top:1173px;width:13px;height:13px;border-radius:50%;background:var(--gold)"></div>
<div class="abs" style="left:623px;top:1173px;width:13px;height:13px;border-radius:50%;background:var(--gold)"></div>
<div class="abs" style="left:647px;top:1173px;width:13px;height:13px;border-radius:50%;background:var(--gold)"></div>
</body>
</html>
```